Yearbook of one of our programs

Our company, Bluewater Circle, www.bluewatercircle.example, hosts leadership programs and workshops for women in leadership roles from different companies all around the world. We need a year book, 11 x 17 inches, we will print with a soft cover, and be approximately 70 pages. Due date for the final completion is 12/9. However, the initial contest & fee is only for pages 1-5, 26-27 and 40-41 (please see attached last year's version). We’d like to use the same color as that. Also attached is the outline we will use once a designer is selected. $50 hourly rate for the completion of the book is set once a designer is confirmed.

```html
<!DOCTYPE html>
<html lang="en">
<head>
<meta charset="utf-8">
<title>Bluewater Circle – Class of 2022 Members</title>
<link rel="stylesheet" href="https://fonts.googleapis.com/css2?family=Great+Vibes&family=Roboto:ital,wght@0,400;0,700;1,700&family=Open+Sans:wght@400;600&display=swap">
<style>
  :root {
    --brand-magenta: #b3335f;
    --ink: #1c1c1c;
    --muted: #555;
    --paper: #f8f7f9;
    --backdrop: #e6e4e7;
    --photo-border: #dcd9de;
    --ornament: #f1d9e3;
  }
  * { box-sizing: border-box; margin: 0; padding: 0; }
  html, body { width: 1200px; height: 789px; overflow: hidden; }
  body {
    background: var(--backdrop);
    font-family: "Roboto", Arial, sans-serif;
    color: var(--ink);
    position: relative;
  }
  .spread {
    position: absolute;
    left: 30px; top: 25px;
    width: 1140px; height: 740px;
    display: flex;
    box-shadow: 0 4px 18px rgba(0,0,0,.18);
  }
  .page {
    position: relative;
    width: 570px; height: 740px;
    background: var(--paper);
    overflow: hidden;
  }
  .page-left { border-right: 1px solid #e2dfe4; }
  .page-header {
    position: absolute; top: 22px; left: 30px;
    display: flex; align-items: flex-end;
    z-index: 1;
  }
  .class-tag {
    background: var(--brand-magenta);
    color: #fff;
    font-family: "Great Vibes", cursive;
    font-size: 34px;
    padding: 8px 22px 6px 18px;
    line-height: 1;
  }
  .section-title {
    font-family: "Great Vibes", cursive;
    font-size: 36px;
    font-weight: 400;
    color: var(--ink);
    margin-left: 12px;
    line-height: 1;
    transform: translateY(10px);
  }
  .members {
    position: absolute; top: 100px; left: 38px;
    display: grid;
    grid-template-columns: repeat(4, 112px);
    grid-auto-rows: 188px;
    column-gap: 18px;
    z-index: 1;
  }
  .member { text-align: center; }
  .member:nth-child(4n+2) { transform: translateY(15px); }
  .member:nth-child(4n+3) { transform: translateY(30px); }
  .member:nth-child(4n+4) { transform: translateY(45px); }
  .member-photo {
    width: 112px; height: 104px;
    border-radius: 10px;
    border: 1px solid var(--photo-border);
    background: linear-gradient(160deg, #8d8a8f 0%, #c9b7a6 55%, #4a4346 100%);
    margin-bottom: 6px;
  }
  .member-photo.tone-light { background: linear-gradient(160deg, #e6e3e6 0%, #d8c2ad 55%, #6d5f5b 100%); }
  .member-photo.tone-dark { background: linear-gradient(160deg, #2f2d31 0%, #a88a77 55%, #2a2628 100%); }
  .member-photo.tone-warm { background: linear-gradient(160deg, #6b3b2a 0%, #d2ad8e 55%, #4b3a35 100%); }
  .member-name { font-weight: 700; font-size: 9.5px; line-height: 1.2; }
  .member-role { font-weight: 700; font-size: 7px; line-height: 1.25; }
  .member-org, .member-city { font-size: 7px; line-height: 1.25; color: var(--muted); }
  .member-status {
    font-weight: 700; font-style: italic; font-size: 7px; line-height: 1.3;
    color: var(--brand-magenta);
  }
  .page-footer {
    position: absolute; left: 0; bottom: 14px;
    width: 250px;
    border-bottom: 7px solid var(--brand-magenta);
    padding: 0 0 4px 40px;
    font-family: "Open Sans", Arial, sans-serif;
    font-size: 12px;
    letter-spacing: .5px;
    color: var(--brand-magenta);
    white-space: nowrap;
    z-index: 1;
  }
  .page-number { color: var(--ink); margin-left: 6px; padding-left: 8px; border-left: 1px solid var(--brand-magenta); }
  .floral {
    position: absolute;
    z-index: 0;
    background: radial-gradient(ellipse at center, var(--ornament) 0%, rgba(241,217,227,0) 70%);
  }
  .floral-left { right: 60px; bottom: 0; width: 130px; height: 60px; }
  .floral-right-bottom { right: 20px; bottom: 20px; width: 130px; height: 150px; }
  .floral-right-top { right: -10px; top: 150px; width: 90px; height: 170px; }
</style>
</head>
<body>
<main class="spread">

  <section class="page page-left">
    <header class="page-header">
      <div class="class-tag">Class of 2022</div>
      <h1 class="section-title">Members</h1>
    </header>

    <div class="floral floral-left" role="img" aria-label="Faint line-drawn flower decoration"></div>

    <div class="members">
      <article class="member">
        <div class="member-photo tone-dark" role="img" aria-label="Portrait photo of Anna Whitfield"></div>
        <p class="member-name">Anna Whitfield</p>
        <p class="member-role">VP, Specialty Solutions</p>
        <p class="member-org">Northvale Health</p>
        <p class="member-city">Bloomfield, CT</p>
        <p class="member-status">Member, 2020 and 2021</p>
      </article>
      <article class="member">
        <div class="member-photo tone-light" role="img" aria-label="Portrait photo of Brooke Ashby"></div>
        <p class="member-name">Brooke Ashby</p>
        <p class="member-role">VP, Finance - Infrastructure</p>
        <p class="member-org">Corvane Mobility</p>
        <p class="member-city">Dublin, Ireland</p>
        <p class="member-status">Founding Member, 2019-2021</p>
      </article>
      <article class="member">
        <div class="member-photo tone-light" role="img" aria-label="Portrait photo of Corinne Adeyemi"></div>
        <p class="member-name">Corinne Adeyemi</p>
        <p class="member-role">President, Global Supply Chain</p>
        <p class="member-org">Prairie Grain Group</p>
        <p class="member-city">Union, KY</p>
        <p class="member-status">New Member, 2021</p>
      </article>
      <article class="member">
        <div class="member-photo tone-warm" role="img" aria-label="Portrait photo of Elena Marsh"></div>
        <p class="member-name">Elena Marsh</p>
        <p class="member-role">GM, Performance Films Business</p>
        <p class="member-org">Halden Materials</p>
        <p class="member-city">St. Louis, MO</p>
        <p class="member-status">New Member, 2021</p>
      </article>

      <article class="member">
        <div class="member-photo" role="img" aria-label="Portrait photo of Gabriela Moreira dos Reis Fontana"></div>
        <p class="member-name">Gabriela Moreira dos Reis Fontana</p>
        <p class="member-role">EVP, Operations, Supply and Quality</p>
        <p class="member-org">Nordenzyme</p>
        <p class="member-city">Skodsborg, Denmark</p>
        <p class="member-status">New Member, 2021</p>
      </article>
      <article class="member">
        <div class="member-photo tone-light" role="img" aria-label="Portrait photo of Hannah Mercer"></div>
        <p class="member-name">Hannah Mercer</p>
        <p class="member-role">SVP, Life Underwriting and New Business</p>
        <p class="member-org">Keystone National Corporation</p>
        <p class="member-city">Greensboro, NC</p>
        <p class="member-status">Founding Member, 2019-2021</p>
      </article>
      <article class="member">
        <div class="member-photo tone-dark" role="img" aria-label="Portrait photo of Julia Danvers"></div>
        <p class="member-name">Julia Danvers</p>
        <p class="member-role">CFO</p>
        <p class="member-org">Harbor Rowe Capital</p>
        <p class="member-city">Baltimore, MD</p>
        <p class="member-status">New Member, 2021</p>
      </article>
      <article class="member">
        <div class="member-photo tone-light" role="img" aria-label="Portrait photo of Jodie Bramwell"></div>
        <p class="member-name">Jodie Bramwell</p>
        <p class="member-role">VP and GM, North America &amp; Global Outdoor, Ranger Denim</p>
        <p class="member-org">Threadline Brands, Inc.</p>
        <p class="member-city">Greensboro, NC</p>
        <p class="member-status">New Member, 2021</p>
      </article>

      <article class="member">
        <div class="member-photo tone-warm" role="img" aria-label="Portrait photo of Kim Tran"></div>
        <p class="member-name">Kim Tran</p>
        <p class="member-role">CFO of North America</p>
        <p class="member-org">Brenton Supply</p>
        <p class="member-city">St. Louis, MO</p>
        <p class="member-status">Founding Member, 2019-2021</p>
      </article>
      <article class="member">
        <div class="member-photo tone-dark" role="img" aria-label="Portrait photo of Lori Ann Maddox"></div>
        <p class="member-name">Lori Ann Maddox</p>
        <p class="member-role">Chief Information Officer, Investment Management Technology</p>
        <p class="member-org">Maple Mutual</p>
        <p class="member-city">Boston, MA</p>
        <p class="member-status">New Member, 2021</p>
      </article>
      <article class="member">
        <div class="member-photo tone-light" role="img" aria-label="Portrait photo of Luciana Ferreira"></div>
        <p class="member-name">Luciana Ferreira</p>
        <p class="member-role">President, Global Specialty Ingredients</p>
        <p class="member-org">Prairie Grain Group</p>
        <p class="member-city">Chicago, IL</p>
        <p class="member-status">Founding Member, 2019-2021</p>
      </article>
      <article class="member">
        <div class="member-photo tone-light" role="img" aria-label="Portrait photo of Laura Bennett"></div>
        <p class="member-name">Laura Bennett</p>
        <p class="member-role">SVP, Finance</p>
        <p class="member-org">Flowpoint</p>
        <p class="member-city">San Jose, CA</p>
        <p class="member-status">Member, 2020 and 2021</p>
      </article>
    </div>

    <footer class="page-footer">BLUEWATER YEARBOOK<span class="page-number">04</span></footer>
  </section>

  <section class="page page-right">
    <header class="page-header">
      <div class="class-tag">Class of 2022</div>
      <h1 class="section-title">Members</h1>
    </header>

    <div class="floral floral-right-top" role="img" aria-label="Faint line-drawn rose decoration"></div>
    <div class="floral floral-right-bottom" role="img" aria-label="Faint line-drawn flower decoration"></div>

    <div class="members">
      <article class="member">
        <div class="member-photo tone-light" role="img" aria-label="Portrait photo of Pauline Verhaegen"></div>
        <p class="member-name">Pauline Verhaegen</p>
        <p class="member-role">VP, Global R&amp;D, Innovation, Sustainability, Chair of EMEA D&amp;I Council</p>
        <p class="member-org">Arden Labels</p>
        <p class="member-city">South Holland, Netherlands</p>
        <p class="member-status">New Member, 2021</p>
      </article>
      <article class="member">
        <div class="member-photo tone-light" role="img" aria-label="Portrait photo of Sara Holloway"></div>
        <p class="member-name">Sara Holloway</p>
        <p class="member-role">CFO and COO</p>
        <p class="member-org">Sealware Brands Corporation</p>
        <p class="member-city">Orlando, FL</p>
        <p class="member-status">Founding Member, 2019-2021</p>
      </article>
      <article class="member">
        <div class="member-photo tone-warm" role="img" aria-label="Portrait photo of Sanne de Groot"></div>
        <p class="member-name">Sanne de Groot</p>
        <p class="member-role">Chief Digital Officer, Europe and Indonesia</p>
        <p class="member-org">Vermeer Retail Group</p>
        <p class="member-city">Wassenaar, Netherlands</p>
        <p class="member-status">Founding Member, 2019-2021</p>
      </article>
      <article class="member">
        <div class="member-photo tone-dark" role="img" aria-label="Portrait photo of Siobhan Reilly"></div>
        <p class="member-name">Siobhan Reilly</p>
        <p class="member-role">Head of Group Actuarial</p>
        <p class="member-org">Maple Mutual</p>
        <p class="member-city">Milton, MA</p>
        <p class="member-status">New Member, 2021</p>
      </article>

      <article class="member">
        <div class="member-photo tone-dark" role="img" aria-label="Portrait photo of Sylvia Hartmann"></div>
        <p class="member-name">Sylvia Hartmann</p>
        <p class="member-role">Chief Manufacturing and Supply Chain Officer</p>
        <p class="member-org">Hollis Electric</p>
        <p class="member-city">Colorado Springs, CO</p>
        <p class="member-status">Founding Member, 2019-2021</p>
      </article>
      <article class="member">
        <div class="member-photo tone-light" role="img" aria-label="Portrait photo of Tamara Dixon"></div>
        <p class="member-name">Tamara Dixon</p>
        <p class="member-role">CPO and VP</p>
        <p class="member-org">Linkwell Connectivity</p>
        <p class="member-city">Singapore</p>
        <p class="member-status">New Member, 2021</p>
      </article>
      <article class="member">
        <div class="member-photo tone-light" role="img" aria-label="Portrait photo of Tessa Kowalski"></div>
        <p class="member-name">Tessa Kowalski</p>
        <p class="member-role">SVP, National Account Services, RPO</p>
        <p class="member-org">Payfield</p>
        <p class="member-city">Atlanta, GA</p>
        <p class="member-status">Founding Member, 2019-2021</p>
      </article>
      <article class="member">
        <div class="member-photo tone-dark" role="img" aria-label="Portrait photo of Tanya Holt"></div>
        <p class="member-name">Tanya Holt</p>
        <p class="member-role">SVP, Merchandising</p>
        <p class="member-org">Grand Market (Vermeer Retail)</p>
        <p class="member-city">Odenton, MD</p>
        <p class="member-status">Founding Member, 2019-2021</p>
      </article>

      <article class="member">
        <div class="member-photo tone-warm" role="img" aria-label="Portrait photo of Trish Keller"></div>
        <p class="member-name">Trish Keller</p>
        <p class="member-role">SVP, Chief Information and Digital Officer</p>
        <p class="member-org">Latchmark</p>
        <p class="member-city">Fishers, IN</p>
        <p class="member-status">Member, 2020 and 2021</p>
      </article>
      <article class="member">
        <div class="member-photo tone-light" role="img" aria-label="Portrait photo of Wanda Brooks"></div>
        <p class="member-name">Wanda Brooks</p>
        <p class="member-role">SVP, Head of ABGA, Co-lead Keystone Financial Securities</p>
        <p class="member-org">Keystone Financial Group</p>
        <p class="member-city">Philadelphia, PA</p>
        <p class="member-status">Member, 2020 and 2021</p>
      </article>
      <article class="member">
        <div class="member-photo" role="img" aria-label="Portrait photo of Willa Morgan"></div>
        <p class="member-name">Willa Morgan</p>
        <p class="member-role">VP, Business Transformation GMO</p>
        <p class="member-org">Fluxon Flow, Inc.</p>
        <p class="member-city">Charlotte, NC</p>
        <p class="member-status">New Member, 2021</p>
      </article>
    </div>

    <footer class="page-footer">BLUEWATER YEARBOOK<span class="page-number">05</span></footer>
  </section>

</main>
</body>
</html>
```